Local Flower Farm Needs Business Card Design

I need business cards designed for a flower farm based in Eudora, Kansas.
Business Info:
We are a local cut flower farm located in Eudora, Kansas, founded by Corinne Haldwick. What started as a passion for agriculture and search for more joy in daily life has blossomed into a small business dedicated to providing the community with beautiful, fresh, and sustainable flowers. We specialize in local, seasonal blooms, ensuring that every petal reflects the care and dedication we pour into our craft. Our mission is to deliver the highest quality flowers directly to our customers through local farmers markets and to florists who share our commitment to sustainability. Join us in celebrating the beauty of nature, one bloom at a time!
Contact Details:
Corinne Haldwick
Owner
Phone 913-555-0147
Facebook: Rosalind Thorpe Gardens
Instagram: @RosalindThorpeGardens
Website: RosalindThorpeGardens.example
Target Market(s)
Wholesale to Florists and Direct to Consumer via Farmers Market
Industry/Entity Type
Florist, Farm
Contact Information for Business Card
Name, Contact Info, Logo
Look and feel
Each slider illustrates characteristics of the customer's brand and the style your logo design should communicate.

```html
<!DOCTYPE html>
<html lang="en">
<head>
<meta charset="utf-8">
<title>Rosalind Thorpe Gardens – Business Card</title>
<link rel="stylesheet" href="https://fonts.googleapis.com/css2?family=Cormorant+Garamond:wght@500&family=Arimo:wght@400;700&display=swap">
<style>
  :root {
    --backdrop: #202020;
    --teal: #0f2a2e;
    --white: #ffffff;
    --ink: #3a3a3a;
    --rule: #c9cfd0;
  }
  * { box-sizing: border-box; margin: 0; padding: 0; }
  html, body { width: 1200px; height: 900px; overflow: hidden; }
  body { background: var(--backdrop); position: relative; font-family: "Arimo", Arial, sans-serif; }

  .card {
    position: absolute;
    width: 560px;
    height: 320px;
    border-radius: 22px;
    overflow: hidden;
    box-shadow: 0 18px 40px rgba(0,0,0,.55);
  }
  .card--back { left: 90px; top: 80px; background: var(--teal); }
  .card--front { left: 550px; top: 500px; background: var(--white); }

  .brand-seal {
    position: absolute;
    display: flex;
    align-items: center;
    justify-content: center;
    text-align: center;
    border-radius: 50%;
    font-family: "Cormorant Garamond", Georgia, serif;
    font-weight: 500;
    text-transform: uppercase;
    letter-spacing: 2px;
    line-height: 1.25;
  }
  .card--back .brand-seal {
    width: 180px; height: 180px;
    left: 190px; top: 70px;
    border: 1.5px solid var(--white);
    color: var(--white);
    font-size: 19px;
  }
  .card--front .brand-seal {
    width: 150px; height: 150px;
    left: 388px; top: 28px;
    background: var(--white);
    border: 1.5px solid var(--teal);
    color: var(--teal);
    font-size: 16px;
  }

  .name-band {
    position: absolute;
    left: 0; right: 0;
    top: 92px; height: 56px;
    background: var(--teal);
    color: var(--white);
    padding: 10px 0 0 34px;
  }
  .name-band__name { font-size: 22px; font-weight: 700; letter-spacing: .5px; }
  .name-band__title { font-size: 13px; margin: 2px 0 0 18px; }

  .contact-list {
    position: absolute;
    left: 90px; top: 210px;
    list-style: none;
    color: var(--ink);
    font-size: 16px;
  }
  .contact-list li { display: flex; align-items: center; gap: 8px; height: 22px; }
  .contact-icon { width: 13px; height: 13px; flex: none; }
</style>
</head>
<body>

<section class="card card--back" aria-label="Card back">
  <div class="brand-seal">Rosalind<br>Thorpe<br>Gardens</div>
</section>

<section class="card card--front" aria-label="Card front">
  <div class="name-band">
    <p class="name-band__name">CORINNE HALDWICK</p>
    <p class="name-band__title">Owner</p>
  </div>
  <div class="brand-seal">Rosalind<br>Thorpe<br>Gardens</div>

  <ul class="contact-list">
    <li>
      <svg class="contact-icon" viewBox="0 0 24 24" aria-hidden="true"><path fill="#0f2a2e" d="M6.6 10.8a15.2 15.2 0 0 0 6.6 6.6l2.2-2.2c.3-.3.7-.4 1-.2 1.1.4 2.3.6 3.6.6.6 0 1 .4 1 1V20c0 .6-.4 1-1 1A17 17 0 0 1 3 4c0-.6.4-1 1-1h3.5c.6 0 1 .4 1 1 0 1.3.2 2.5.6 3.6.1.3 0 .7-.2 1z"/></svg>
      (913)555-0147
    </li>
    <li>
      <svg class="contact-icon" viewBox="0 0 12 12" aria-hidden="true"><circle cx="6" cy="6" r="6" fill="#0f2a2e"/></svg>
      Rosalind Thorpe Gardens
    </li>
    <li>
      <svg class="contact-icon" viewBox="0 0 12 12" aria-hidden="true"><circle cx="6" cy="6" r="6" fill="#0f2a2e"/></svg>
      @RosalindThorpeGardens
    </li>
    <li>
      <svg class="contact-icon" viewBox="0 0 12 12" aria-hidden="true"><circle cx="6" cy="6" r="6" fill="#0f2a2e"/></svg>
      RosalindThorpeGardens.example
    </li>
  </ul>
</section>

</body>
</html>
```